"Cedar Hollow Realty" is the name of my real estate company

This is for a: "for sale" sign, looking for a minimalist design, wire frame outline of a midcentury modern homes roof line or elevation?

My name is: Dean Marlowe (needed)
My Cell # is: 415 208 3947 (needed)
My BRE license # is: 02468135 (needed)
BRE needs to be displayed in this format: BRE 02468135 (needed)
The white outline on the sign riders 'pictured" may work on large sign
Note font on pictured rider sign

This design is for a real estate "for sale" sign or sandwich board sign. Do Not include the words "For Sale" on the sign.

The measurements are 36" inches (91.44 cm) Length, or tall X 24" inches (60.90 cm) Wide.

|
3
---- 24 ----
6
|

Sorry I wasn't more specific earlier. I'd like the elements of the sign to be scaled in size according to their importance, from largest to smallest:

My name: Dean Marlowe
My phone number: 415-208-3947
My company name: Cedar Hollow Realty
My license number: BRE 02468135 (This can be much smaller than the smallest text)
Additionally, please incorporate contemporary to mid-century modern elements on the wire frame roofline or a simple roof-like design.

Thank you!

Best regards,
Dean

```html
<!DOCTYPE html>
<html lang="en">
<head>
<meta charset="UTF-8">
<title>Cedar Hollow Realty — Dean Marlowe Sign</title>
<link rel="stylesheet" href="https://fonts.googleapis.com/css2?family=Poppins:wght@400;600&display=swap">
<style>
  :root {
    --sign-black: #000000;
    --ink-white: #ffffff;
    --rule-glow: rgba(255, 255, 255, 0.95);
    --roof-tone: #1a1a1a;
  }
  * { margin: 0; padding: 0; box-sizing: border-box; }
  html, body {
    width: 867px;
    height: 1200px;
    overflow: hidden;
    background: var(--sign-black);
  }
  .sign {
    position: relative;
    width: 867px;
    height: 1200px;
    background: var(--sign-black);
    color: var(--ink-white);
    font-family: "Poppins", sans-serif;
  }
  .sign__frame {
    position: absolute;
    left: 72px;
    top: 66px;
    right: 72px;
    bottom: 66px;
    border: 1.5px solid var(--ink-white);
  }
  .brand {
    position: absolute;
    top: 232px;
    left: 0;
    width: 100%;
    text-align: center;
    font-weight: 600;
    font-size: 50px;
    line-height: 1.08;
    letter-spacing: 0.5px;
    text-transform: uppercase;
  }
  .agent-name {
    position: absolute;
    top: 512px;
    left: 0;
    width: 100%;
    text-align: center;
    font-weight: 400;
    font-size: 62px;
    line-height: 1;
  }
  .rule {
    position: absolute;
    left: 166px;
    width: 535px;
    height: 2px;
    background: linear-gradient(90deg, transparent 0%, var(--rule-glow) 50%, transparent 100%);
  }
  .rule--upper { top: 634px; }
  .rule--lower { top: 736px; }
  .agent-phone {
    position: absolute;
    top: 652px;
    left: 0;
    width: 100%;
    text-align: center;
    font-weight: 400;
    font-size: 54px;
    line-height: 1;
    letter-spacing: 1px;
  }
  .agent-license {
    position: absolute;
    top: 776px;
    left: 0;
    width: 100%;
    text-align: center;
    font-weight: 400;
    font-size: 23px;
    line-height: 1;
  }
  .roofline {
    position: absolute;
    left: 132px;
    top: 968px;
    width: 598px;
    height: 166px;
    background: linear-gradient(180deg, var(--sign-black) 0%, var(--roof-tone) 100%);
  }
</style>
</head>
<body>
  <main class="sign">
    <div class="sign__frame"></div>

    <h1 class="brand">Cedar Hollow<br>Realty</h1>

    <p class="agent-name">Dean MARLOWE</p>
    <div class="rule rule--upper"></div>
    <p class="agent-phone">415-208-3947</p>
    <div class="rule rule--lower"></div>
    <p class="agent-license">BRE 02468135</p>

    <div class="roofline" role="img" aria-label="White wireframe outline of a mid-century modern house roofline with chimney and gables"></div>
  </main>
</body>
</html>
```